Provide bookkeeping and accounting services to small and growing businesses

We need website and logo design using the name Dornaby as the logo.
The target audience are small companies and startups who need:
1) Simple bookkeeping services
2) Accounting advice that only someone with many years of senior financial experience as a CPA can provide.

The services are provided by two individuals. each of whom specialize in one of the areas.

We want the website to be clean without a lot of visual distraction but don't know how to make a boring subject interesting. We believe our potential clients, small business owners, need to find what they want quickly and easily without a lot of verbiage or distractions.

We've attached a draft of the homepage and have completed the text on most of the other pages.

Target Market(s)

small and early stage growth companies in San Diego North County

Industry/Entity Type

Accounting

Number of Pages Required

1 page

Font styles to use
Sans Serif

Colors
86cfc6
33b8a4
85cae6

Requirements
Must have
• We need a design for the website homepage that includes the name Dornaby as the logo. Must include a design for the name.
• Must have color in teal or greenish blue.
Nice to have
• White background, clean, clear, uncluttered.
• We would like to use the design in a Theme on a WordPress website. Themes Paper Lantern and Quiet Harbour are appealing to us.
Should not have
• Moving pictures

```html
<!DOCTYPE html>
<html lang="en">
<head>
<meta charset="utf-8">
<title>Dornaby Accounting &amp; Bookkeeping</title>
<link href="https://fonts.googleapis.com/css2?family=Raleway:wght@400;500;600;700&family=Open+Sans:wght@400;600&display=swap" rel="stylesheet">
<style>
:root{
  --teal:#33b8a4;
  --teal-soft:#86cfc6;
  --sky:#85cae6;
  --nav:#3fb9a9;
  --ink:#333c44;
  --muted:#7a848c;
  --footer:#3aab9d;
  --footer-dark:#2f9386;
  --white:#ffffff;
}
*{box-sizing:border-box;margin:0;padding:0}
html,body{width:1200px;height:2252px;overflow:hidden}
body{font-family:"Open Sans",Arial,sans-serif;color:var(--ink);background:var(--white)}
h1,h2,h3,h4,.brand,.btn,.main-nav{font-family:"Raleway",Arial,sans-serif}

.site-header{height:100px;display:flex;justify-content:space-between;align-items:center;padding:0 72px}
.brand{line-height:1.05}
.brand-name{font-size:34px;font-weight:700;color:var(--teal)}
.brand-tag{font-size:26px;font-weight:500;color:var(--ink)}
.contact-lines{font-size:17px;color:var(--ink)}
.contact-lines div{display:flex;align-items:center;gap:10px;margin:6px 0}
.contact-lines svg{width:20px;height:20px}

.main-nav{height:40px;background:var(--nav);display:flex;justify-content:space-between;align-items:center;padding:0 80px}
.main-nav a{color:var(--white);text-decoration:none;font-size:15px;font-weight:600;letter-spacing:.5px}

.hero{position:relative;height:460px;background:linear-gradient(180deg,#8fc4ea 0%,#b8d8ee 35%,#7a93a8 62%,#4f7a94 78%,#6aa0b8 100%)}
.hero h1{position:absolute;top:190px;width:100%;text-align:center;color:var(--white);font-size:50px;font-weight:600;line-height:1.2;text-shadow:0 2px 6px rgba(0,0,0,.35)}
.hero-dots{position:absolute;bottom:20px;left:0;right:0;display:flex;justify-content:center;gap:10px}
.hero-dots span{width:12px;height:12px;border-radius:50%;background:rgba(255,255,255,.6)}
.hero-dots span.on{background:var(--white)}
.hero-notch{position:absolute;bottom:-1px;left:574px;width:0;height:0;border-left:26px solid transparent;border-right:26px solid transparent;border-bottom:22px solid #8dd0ea}

.welcome{height:288px;background:linear-gradient(180deg,#8dd0ea,#a9dcef);text-align:center;padding:38px 150px 0}
.welcome h2{color:var(--white);font-size:36px;font-weight:600}
.welcome p{color:var(--white);font-size:14px;line-height:1.7;margin:18px auto 22px;max-width:860px}
.btn{display:inline-block;background:var(--teal);color:var(--white);font-size:14px;font-weight:600;padding:10px 28px;border-radius:22px;letter-spacing:.5px}

.services{height:472px;text-align:center;padding-top:40px;background:var(--white)}
.section-title{font-size:38px;font-weight:600;color:var(--ink)}
.section-intro{font-size:14px;line-height:1.7;color:var(--muted);max-width:720px;margin:16px auto 0}
.service-cards{display:flex;justify-content:center;gap:56px;margin-top:50px}
.card{position:relative;width:330px;height:190px;background:linear-gradient(180deg,#86cfc6,#33b8a4);border-radius:10px;color:var(--white);padding:62px 30px 0}
.card-icon{position:absolute;top:-34px;left:131px;width:68px;height:68px;border-radius:10px;background:var(--white);box-shadow:0 2px 8px rgba(0,0,0,.15);display:flex;align-items:center;justify-content:center}
.card h3{font-size:22px;font-weight:600}
.card p{font-size:13px;line-height:1.6;margin-top:12px}

.resources{height:280px;text-align:center;padding-top:40px;background:linear-gradient(120deg,#3b4650,#5b6870 45%,#3e4a54)}
.resources .section-title{color:var(--sky)}
.resources .section-intro{color:#e6ecef}
.resources .btn{margin-top:22px}

.experience{height:340px;display:flex;gap:40px;padding:40px 72px 0}
.experience-photo{width:320px;height:232px;background:linear-gradient(135deg,#d9e4ec,#9ab7c8 55%,#e7edf1)}
.experience-body{flex:1}
.experience-body .section-title{font-size:40px;text-align:left}
.experience-body p{font-size:14px;line-height:1.7;color:var(--muted);margin:12px 0 22px}

.site-footer{height:232px;background:var(--footer);color:var(--white);display:flex;padding:28px 72px 0;gap:40px}
.footer-col{flex:1}
.footer-col h4{font-size:17px;font-weight:600;letter-spacing:1px;margin-bottom:14px}
.footer-col li{list-style:none;font-size:13px;line-height:2;display:flex;align-items:center;gap:8px}
.footer-col li::before{content:"";width:10px;height:10px;border-radius:50%;background:var(--white);flex:none}
.footer-col.plain li::before,.footer-col.social li::before,.footer-col.contact li::before{display:none}
.nav-grid{display:grid;grid-template-columns:1fr 1fr;font-size:13px;line-height:2}
.social-dot{width:28px;height:28px;border-radius:50%;background:var(--white);flex:none}
.footer-col.social li{line-height:2.8}
.footer-bottom{height:40px;background:var(--footer-dark);color:#d8f0ec;font-size:12px;text-align:center;line-height:40px}
</style>
</head>
<body>
<header class="site-header">
  <div class="brand">
    <div class="brand-name">Dornaby</div>
    <div class="brand-tag">Accounting &amp; Bookkeeping</div>
  </div>
  <div class="contact-lines">
    <div><svg viewBox="0 0 20 20"><rect width="20" height="20" rx="3" fill="#33b8a4"/><path d="M6 5l2 0 1 3-1.2 1a7 7 0 003.2 3.2l1-1.2 3 1v2c0 .6-.4 1-1 1A9 9 0 015 6c0-.6.4-1 1-1z" fill="#fff"/></svg>1-800-555-0148</div>
    <div><svg viewBox="0 0 20 20"><rect width="20" height="20" rx="3" fill="#33b8a4"/><rect x="4" y="6" width="12" height="8" fill="none" stroke="#fff" stroke-width="1.4"/><path d="M4 6l6 5 6-5" fill="none" stroke="#fff" stroke-width="1.4"/></svg>hello@dornaby-example.com</div>
  </div>
</header>

<nav class="main-nav">
  <a>HOME</a><a>ABOUT US</a><a>SERVICES</a><a>EXPERIENCE</a><a>RESOURCES</a><a>CONTACT US</a>
</nav>

<section class="hero" role="img" aria-label="City skyline across the bay under a blue sky">
  <h1>We are an Accounting &amp; Bookkeeping<br>based in San Diego</h1>
  <div class="hero-dots"><span></span><span class="on"></span><span></span></div>
  <div class="hero-notch"></div>
</section>

<section class="welcome">
  <h2>Welcome to Dornaby Accounting &amp; Bookkeeping</h2>
  <p>Dornaby offers a flexible range of accounting and bookkeeping services and support for small and growing companies in San Diego North County. We provide bookkeeping services specializing in small businesses so you can focus on running your business. We also provide a broad range of accounting services to meet your needs.</p>
  <span class="btn">LEARN MORE</span>
</section>

<section class="services">
  <h2 class="section-title">Our Services</h2>
  <p class="section-intro">Clear, dependable support for your books and finances. We keep records accurate, reports timely and advice practical so owners can make confident decisions and grow.</p>
  <div class="service-cards">
    <div class="card">
      <div class="card-icon"><svg width="34" height="34" viewBox="0 0 34 34"><rect x="7" y="4" width="20" height="26" rx="2" fill="#444"/><rect x="10" y="8" width="14" height="3" fill="#fff"/></svg></div>
      <h3>Book Keeping</h3>
      <p>Accurate monthly records, reconciled accounts and simple reports.</p>
    </div>
    <div class="card">
      <div class="card-icon"><svg width="36" height="34" viewBox="0 0 36 34"><circle cx="18" cy="11" r="6" fill="#444"/><path d="M8 30a10 10 0 0120 0z" fill="#444"/><circle cx="7" cy="14" r="4" fill="#444"/><circle cx="29" cy="14" r="4" fill="#444"/></svg></div>
      <h3>Financial Advice</h3>
      <p>Senior CPA guidance on planning, cash flow and growth.</p>
    </div>
    <div class="card">
      <div class="card-icon"><svg width="30" height="34" viewBox="0 0 30 34"><rect x="3" y="2" width="24" height="30" rx="2" fill="#444"/><rect x="7" y="6" width="16" height="6" fill="#fff"/><g fill="#fff"><rect x="7" y="16" width="4" height="4"/><rect x="13" y="16" width="4" height="4"/><rect x="19" y="16" width="4" height="4"/><rect x="7" y="23" width="4" height="4"/><rect x="13" y="23" width="4" height="4"/><rect x="19" y="23" width="4" height="4"/></g></svg></div>
      <h3>Accounting Service</h3>
      <p>Year-end statements, tax preparation and compliance support.</p>
    </div>
  </div>
</section>

<section class="resources" role="img" aria-label="Desk with laptop and financial papers in dark tones">
  <h2 class="section-title">Resources</h2>
  <p class="section-intro">Helpful guides, checklists and templates for small business owners. Find quick answers on records, payroll, taxes and planning for the year ahead.</p>
  <span class="btn">LEARN MORE</span>
</section>

<section class="experience">
  <div class="experience-photo" role="img" aria-label="Hands working with a calculator and charts on a desk"></div>
  <div class="experience-body">
    <h2 class="section-title">Experience</h2>
    <p>Our two specialists bring many years of hands-on work with small and early stage companies. One focuses on daily bookkeeping that keeps your records clean and current. The other is a CPA with senior financial experience who advises on budgets, funding, reporting and the decisions that shape growth. Together we give you clear numbers and practical advice without jargon.</p>
    <span class="btn">LEARN MORE</span>
  </div>
</section>

<footer class="site-footer">
  <div class="footer-col">
    <h4>LATEST NEWS</h4>
    <ul>
      <li>New quarterly filing dates</li>
      <li>Simple payroll tips for owners</li>
      <li>Year end checklist ready</li>
      <li>Startup funding basics explained</li>
    </ul>
  </div>
  <div class="footer-col">
    <h4>NAVIGATION</h4>
    <div class="nav-grid"><span>Home</span><span>Resources</span><span>About Us</span><span>Contact Us</span><span>Services</span><span></span><span>Experience</span></div>
  </div>
  <div class="footer-col contact">
    <h4>CONTACT US</h4>
    <ul>
      <li>DORNABY LLC</li>
      <li>214 Harbor View Lane</li>
      <li>North County, CA 92000</li>
      <li>1-800-555-0148</li>
      <li>hello@dornaby-example.com</li>
    </ul>
  </div>
  <div class="footer-col social">
    <h4>CONNECT US</h4>
    <ul>
      <li><span class="social-dot"></span>Community</li>
      <li><span class="social-dot"></span>Updates</li>
      <li><span class="social-dot"></span>Network</li>
    </ul>
  </div>
</footer>
<div class="footer-bottom">Copyright © 2024 Dornaby. All Rights Reserved.</div>
</body>
</html>
```